Stonebrace Business Card Design

The Stonebrace Co is an aggregate (crushing) equipment dealer serving Western Canadian provinces. Stonebrace is a distributor of aggregate equipment for different manufacturers.

We are looking to change and update the existing business card which has been used since the existence of the company. A copy of existing card has been attached for reference. The Stonebrace Co logo we want to remain the same and we want the green color to remain the same.

We are wanting something new with a different look. A refreshing card to show a new modern and updated look. No longer wanting to have the manufacturers on the back of the card but something more like our logo on the back of the card with a statement like "Crushing Solutions"

ideas could be:
- card can be different colors on front and back
- front or reverse of the card could possibly be the green color with the logo in black

Target Market(s)

Owners of Aggregate/Crushing companies

Contact Information for Business Card

see above

Requirements
Must have
• - logo to remain same along with same font within logo
• - green color to remain same
Nice to have
• as noted above under project description
Should not have

```html
<!DOCTYPE html>
<html lang="en">
<head>
<meta charset="utf-8">
<title>Stonebrace Business Card</title>
<link rel="stylesheet" href="https://fonts.googleapis.com/css2?family=Roboto:wght@400;500;700&family=Roboto+Condensed:wght@700&display=swap">
<style>
  :root {
    --brand-green: #8a8b0c;
    --ink: #222221;
    --ink-soft: #5f5f5f;
    --card-white: #f6f6f4;
    --backdrop: #e8e5de;
  }
  * { box-sizing: border-box; margin: 0; padding: 0; }
  html, body {
    width: 1200px; height: 960px; overflow: hidden;
    background: var(--backdrop);
    font-family: "Roboto", Arial, sans-serif;
  }
  .canvas { position: relative; width: 1200px; height: 960px; }

  .card {
    position: absolute; left: 320px; width: 600px; border-radius: 20px;
  }
  .card--front { top: 100px; height: 350px; background: var(--brand-green); }
  .card--back  { top: 493px; height: 342px; background: var(--card-white); overflow: hidden; }

  .wordmark {
    position: absolute; font-weight: 700; color: var(--ink);
    letter-spacing: 0.2px; white-space: nowrap;
  }
  .card--front .brand-dot {
    position: absolute; left: 135px; top: 158px; width: 44px; height: 44px;
    border-radius: 50%; background: var(--ink);
  }
  .card--front .wordmark { left: 249px; top: 167px; font-size: 22px; }
  .tagline {
    position: absolute; left: 0; right: 0; top: 299px; text-align: center;
    font-size: 15px; font-weight: 500; color: var(--ink);
  }

  .card--back .brand-dot {
    position: absolute; right: 60px; top: 30px; width: 64px; height: 64px;
    border-radius: 50%; background: var(--brand-green);
  }
  .card--back .wordmark { right: 30px; top: 116px; font-size: 17px; }

  .person { position: absolute; left: 32px; top: 190px; }
  .person-name {
    font-family: "Roboto Condensed", Arial, sans-serif; font-weight: 700;
    font-size: 20px; color: var(--brand-green); line-height: 24px;
  }
  .person-title { font-size: 14.5px; font-weight: 500; color: var(--ink); line-height: 22px; }
  .person-address { margin-top: 5px; font-size: 14px; color: var(--ink-soft); line-height: 20px; }

  .contact-list {
    position: absolute; right: 34px; top: 197px; list-style: none;
    font-size: 14px; color: var(--ink-soft); line-height: 20px; text-align: right;
  }
  .contact-list li { display: flex; justify-content: flex-end; align-items: center; gap: 7px; }
  .contact-list svg { width: 13px; height: 13px; fill: var(--brand-green); }

  .rule {
    position: absolute; left: 0; right: 0; top: 303px; height: 2px; background: var(--brand-green);
  }
  .web-pill {
    position: absolute; left: 33px; top: 289px; width: 240px; height: 28px;
    border-radius: 14px; background: var(--brand-green); color: #fff;
    font-size: 14px; letter-spacing: 2.6px; text-align: center; line-height: 28px;
  }
</style>
</head>
<body>
<main class="canvas">
  <section class="card card--front">
    <span class="brand-dot"></span>
    <span class="wordmark">THE STONEBRACE CO.</span>
    <p class="tagline">Crushing Solutions</p>
  </section>

  <section class="card card--back">
    <span class="brand-dot"></span>
    <span class="wordmark">THE STONEBRACE CO.</span>

    <div class="person">
      <p class="person-name">REID HALVORSEN</p>
      <p class="person-title">CEO/FOUNDER</p>
      <p class="person-address">2218- 48B Avenue<br>Leduc, Alberta T9E 3K7</p>
    </div>

    <ul class="contact-list">
      <li>780.555.0142
        <svg viewBox="0 0 16 16"><path d="M3.6 1.2l2.4 2.9-1.3 1.8c.9 2 2.4 3.5 4.4 4.4l1.8-1.3 2.9 2.4-1.3 2.6C7 13.6 2.4 9 2.4 2.5z"/></svg></li>
      <li>780.555.0187
        <svg viewBox="0 0 16 16"><path d="M4 0h8v16H4zM5.5 1.5v11h5v-11zM7.2 13.6h1.6v1.2H7.2z" fill-rule="evenodd"/></svg></li>
      <li>780.555.0163
        <svg viewBox="0 0 16 16"><path d="M4 1h8v4H4zM1 6h14v6h-3v3H4v-3H1zM5.5 10v3.5h5V10z" fill-rule="evenodd"/></svg></li>
      <li>reid@stonebr.com
        <svg viewBox="0 0 16 16"><path d="M1 3h14v1.2L8 8.6 1 4.2zM1 5.8l7 4.4 7-4.4V13H1z"/></svg></li>
    </ul>

    <div class="rule"></div>
    <p class="web-pill">www.stonebrace.ca</p>
  </section>
</main>
</body>
</html>
```